Classy, Elegant, Simple Business Card Design

Looking to have a classy, simple, and elegant design. Want a top notch designed business card. I really like the look of the new torvane credit card. I also like the design I attached. I am trying to reach 21-29 year old females for booking us for there wedding or event. We offer Disc Jockey Service, Photo Booth Rentals, and Uplighting .

Target Market(s)

21-28 year old females

Contact Information for Business Card

Has to have logo, website, email, and phone number

Font styles to use
Other font styles liked:
• open to font choice, modern, clean
Designer to choose
33a6d7
0791cd
0555a3
ffffff

Requirements
Must have
• Has to have logo, website, email, and phone number
Nice to have
• I really like the design of the new torvane credit card. I also included my logo and some designs I like
Should not have
• clutter or too much info

```html
<!DOCTYPE html>
<html lang="en">
<head>
<meta charset="utf-8">
<title>Tidewell Event Group – Business Card</title>
<link href="https://fonts.googleapis.com/css2?family=Poppins:wght@400;500;600&display=swap" rel="stylesheet">
<style>
  :root {
    --sky: #33a6d7;
    --azure: #0791cd;
    --navy: #0555a3;
    --white: #ffffff;
    --ink: #3d4450;
    --muted: #8a9099;
    --stage: #d9dadc;
  }
  * { margin: 0; padding: 0; box-sizing: border-box; }
  html, body { width: 1200px; height: 801px; overflow: hidden; }
  body {
    background: var(--stage);
    font-family: "Poppins", sans-serif;
    position: relative;
  }
  .card {
    position: absolute;
    top: 246px;
    width: 540px;
    height: 309px;
    overflow: hidden;
    box-shadow: 0 10px 28px rgba(0,0,0,.18);
  }
  .card--front { left: 40px; background: var(--white); }
  .card--back {
    left: 620px;
    background: radial-gradient(ellipse at 45% 40%, var(--sky) 0%, var(--azure) 55%, #0a74bd 100%);
    display: flex; align-items: center; justify-content: center;
  }
  .card__swoosh { position: absolute; inset: 0; }

  .brand {
    position: absolute; top: 22px; left: 150px;
    display: flex; align-items: center; gap: 10px;
  }
  .brand__dot { width: 14px; height: 14px; border-radius: 50%; background: var(--azure); }
  .brand__name {
    font-weight: 600; font-size: 20px; line-height: 1.1; color: var(--azure);
    letter-spacing: .5px;
  }

  .services {
    position: absolute; top: 150px; left: 380px;
    list-style: none; font-size: 12px; color: var(--ink); line-height: 1.5;
  }
  .services li::before {
    content: ""; display: inline-block; width: 4px; height: 4px; border-radius: 50%;
    background: var(--azure); margin-right: 7px; vertical-align: middle;
  }

  .contact { position: absolute; left: 34px; top: 204px; }
  .contact__name { font-weight: 600; font-size: 19px; color: var(--azure); line-height: 1.1; }
  .contact__title { font-size: 11px; color: var(--muted); margin-bottom: 8px; }
  .contact__line {
    display: flex; align-items: center; gap: 8px;
    font-size: 12px; color: var(--ink); line-height: 1.5;
  }
  .contact__icon { width: 11px; height: 11px; flex: none; }

  .back__name {
    font-weight: 600; font-size: 58px; color: var(--navy); letter-spacing: 1px;
  }
</style>
</head>
<body>

<section class="card card--front" aria-label="Business card front">
  <svg class="card__swoosh" viewBox="0 0 540 309" aria-hidden="true">
    <path d="M0 180 C140 174 250 120 350 84 S480 36 540 28 L540 40 C480 48 440 66 354 98 S140 190 0 194 Z" fill="var(--azure)"/>
    <path d="M0 168 C140 162 250 108 346 72 S476 22 540 14 L540 19 C476 28 440 50 348 78 S140 170 0 173 Z" fill="var(--sky)"/>
  </svg>

  <div class="brand">
    <span class="brand__dot"></span>
    <span class="brand__name">Tidewell<br>Event Group</span>
  </div>

  <ul class="services">
    <li>Disc Jockey Service</li>
    <li>Photo Booth Rentals</li>
    <li>Uplighting</li>
  </ul>

  <div class="contact">
    <p class="contact__name">Daniel Reyes</p>
    <p class="contact__title">President</p>
    <p class="contact__line">
      <svg class="contact__icon" viewBox="0 0 12 12" aria-hidden="true"><path d="M3 1 L5 3.5 L4 5 C4.8 6.6 5.6 7.4 7 8 L8.5 7 L11 9 L9.5 11 C5 10.5 1.5 7 1 2.5 Z" fill="var(--azure)"/></svg>
      555-204-7731
    </p>
    <p class="contact__line">
      <svg class="contact__icon" viewBox="0 0 12 12" aria-hidden="true"><rect x="1" y="2.5" width="10" height="7" rx="1" fill="var(--azure)"/><path d="M1.5 3 L6 6.5 L10.5 3" stroke="var(--white)" fill="none" stroke-width="1"/></svg>
      info@tidewellevents.com
    </p>
    <p class="contact__line">
      <svg class="contact__icon" viewBox="0 0 12 12" aria-hidden="true"><circle cx="6" cy="6" r="5" fill="var(--azure)"/><path d="M1 6 H11 M6 1 C3.5 4 3.5 8 6 11 M6 1 C8.5 4 8.5 8 6 11" stroke="var(--white)" fill="none" stroke-width=".8"/></svg>
      www.tidewellevents.com
    </p>
  </div>
</section>

<section class="card card--back" aria-label="Business card back">
  <span class="back__name">Tidewell</span>
</section>

</body>
</html>
```